Gobal construction supply company needs new business card design

I need a business card design for my global supply company using an existing logo. i will be looking to print these on rounded corner cards with the black background version of my logo on the back. on the front white background, my logo again and my simple details.

```html
<!DOCTYPE html>
<html lang="en">
<head>
<meta charset="UTF-8">
<title>Meridian Build Supply – Business Card</title>
<link rel="stylesheet" href="https://fonts.googleapis.com/css2?family=Jost:wght@500&family=Open+Sans:wght@400;600;700&display=swap">
<style>
  :root {
    --backdrop: #2a2a2a;
    --card-white: #f3f3f3;
    --brand-red: #d40000;
    --ink: #1a1a1a;
    --text-grey: #333333;
    --rule-grey: #a8a8a8;
    --white: #ffffff;
  }
  * { margin: 0; padding: 0; box-sizing: border-box; }
  html, body { width: 1200px; height: 1200px; overflow: hidden; }
  body {
    position: relative;
    background: var(--backdrop);
    font-family: "Open Sans", Arial, sans-serif;
  }
  .card {
    position: absolute;
    top: 310px;
    height: 594px;
    border-radius: 22px;
    text-align: center;
  }
  .card-front { left: 234px; width: 364px; background: var(--card-white); }
  .card-back { left: 628px; width: 367px; background: var(--brand-red); }

  .brand-mark {
    position: absolute;
    left: 0; right: 0;
    top: 120px;
    font-weight: 700;
    font-size: 50px;
    line-height: 56px;
    letter-spacing: 1px;
    color: var(--ink);
  }
  .brand-name {
    position: absolute;
    left: 0; right: 0;
    top: 196px;
    font-weight: 700;
    font-size: 22px;
    line-height: 26px;
    color: var(--ink);
    letter-spacing: -0.2px;
  }
  .brand-tagline {
    position: absolute;
    left: 0; right: 0;
    top: 224px;
    display: flex;
    justify-content: center;
    align-items: center;
    gap: 6px;
    font-size: 14px;
    line-height: 18px;
    letter-spacing: 6px;
    color: var(--brand-red);
  }
  .brand-tagline::before, .brand-tagline::after {
    content: "";
    width: 56px;
    height: 2px;
    background: var(--brand-red);
  }

  .person {
    position: absolute;
    left: 0; right: 0;
    top: 330px;
  }
  .person-name {
    font-family: "Jost", sans-serif;
    font-weight: 500;
    font-size: 27px;
    letter-spacing: 0.5px;
    color: var(--brand-red);
    line-height: 1.1;
  }
  .person-role {
    font-size: 17px;
    color: var(--text-grey);
    line-height: 1.2;
  }
  .divider {
    width: 208px;
    height: 1px;
    margin: 7px auto 0;
    background: var(--rule-grey);
  }
  .contact {
    list-style: none;
    margin-top: 12px;
    font-size: 17px;
    line-height: 21.5px;
    color: var(--text-grey);
  }
  .contact .label { color: var(--brand-red); font-weight: 600; }
  .contact .web { color: var(--brand-red); font-weight: 600; }
  .address {
    margin-top: 8px;
    padding-top: 5px;
    font-size: 17px;
    line-height: 21.5px;
    color: var(--text-grey);
    font-style: normal;
  }

  .back-mark {
    position: absolute;
    left: 0; right: 0;
    top: 250px;
    font-weight: 700;
    font-size: 68px;
    line-height: 76px;
    letter-spacing: 2px;
    color: var(--white);
  }
  .back-web {
    position: absolute;
    left: 0; right: 0;
    top: 522px;
    font-weight: 600;
    font-size: 17px;
    letter-spacing: 0.6px;
    color: var(--white);
  }
</style>
</head>
<body>
  <section class="card card-front">
    <div class="brand-mark">MBS</div>
    <div class="brand-name">MERIDIAN BUILD SUPPLY</div>
    <div class="brand-tagline">WORLDWIDE</div>
    <div class="person">
      <h1 class="person-name">DANIEL HART</h1>
      <p class="person-role">Managing Director</p>
      <div class="divider"></div>
      <ul class="contact">
        <li><span class="label">P:</span> 044-987 654 321</li>
        <li><span class="label">M:</span> 044-987 654 321</li>
        <li><span class="label">E:</span> hello@meridianbuild.com</li>
        <li class="web">www.meridianbuild.com</li>
      </ul>
      <div class="divider"></div>
      <address class="address">48 Harbour Road, Dockside<br>Portland Bay, 402156.</address>
    </div>
  </section>

  <section class="card card-back">
    <div class="back-mark">MBS</div>
    <p class="back-web">www.meridianbuild.com</p>
  </section>
</body>
</html>
```